Banner Pop Up Opt In Form REDESIGNS - SLEEK BLACK LOOK

Please redesign banners attached.

I am looking for a very sleek look....I do not like this collage of images on these current designs. Please keep all content same but use images that pop.

I have an acccount at www.pixvane-example.com or you can use your own images.

I like black background for somereason because it looks very sleek....but these designs should pop , build trust and credibility and have easy opt in form....SLEEK AND MODERN LOOK is what im looking for....

Target Market(s)

Consumers on websites

Requirements
Must have
• Please redesign banners attached.

Nice to have

Should not have

```html
<!DOCTYPE html>
<html lang="en">
<head>
<meta charset="utf-8">
<title>Smart Fitness Watch Offer</title>
<link rel="stylesheet" href="https://fonts.googleapis.com/css2?family=Poppins:wght@300;400;500;700;800&display=swap">
<style>
  :root {
    --ink: #000000;
    --accent: #f7a11d;
    --paper: #ffffff;
    --photo-base: #4d5253;
    --photo-window: #8d9292;
    --photo-shirt: #7c6c70;
    --photo-teal: #4f6362;
    --photo-blush: #86666b;
    --photo-floor: #2c3032;
    --device-light: #3a3a3a;
    --device-dark: #141414;
  }
  * { margin: 0; padding: 0; box-sizing: border-box; }
  html, body { width: 1200px; height: 1200px; overflow: hidden; }
  body { font-family: "Poppins", Arial, sans-serif; color: var(--paper); }
  .banner { position: relative; width: 1200px; height: 1200px; overflow: hidden; }
  .workout-photo {
    position: absolute; inset: 0;
    background:
      radial-gradient(ellipse 260px 380px at 1130px 180px, var(--photo-window) 0%, rgba(141,146,146,0) 100%),
      radial-gradient(ellipse 300px 260px at 820px 700px, var(--photo-shirt) 0%, rgba(124,108,112,0) 100%),
      radial-gradient(ellipse 260px 320px at 1080px 620px, var(--photo-teal) 0%, rgba(79,99,98,0) 100%),
      radial-gradient(ellipse 220px 160px at 300px 790px, var(--photo-blush) 0%, rgba(134,102,107,0) 100%),
      radial-gradient(ellipse 420px 200px at 500px 680px, #7d8384 0%, rgba(125,131,132,0) 100%),
      linear-gradient(180deg, rgba(44,48,50,0) 55%, var(--photo-floor) 100%),
      linear-gradient(160deg, #656a6b 0%, var(--photo-base) 60%, #3a3e40 100%);
  }
  .header-shape { position: absolute; left: 0; top: 0; width: 1200px; height: 700px; }
  .headline {
    position: absolute; left: 55px; top: 46px;
    font-weight: 800; font-size: 67px; line-height: 1; letter-spacing: 1px;
    color: var(--accent);
  }
  .subhead {
    position: absolute; left: 56px; top: 122px;
    font-weight: 400; font-size: 27.5px; line-height: 1; letter-spacing: 0.1px;
  }
  .product-photo {
    position: absolute; left: 62px; top: 196px; width: 258px; height: 322px;
    border-radius: 40px 40px 30px 30px;
    background: radial-gradient(ellipse at 50% 40%, var(--device-light) 0%, var(--device-dark) 75%);
  }
  .product-name { position: absolute; left: 364px; top: 238px; }
  .product-name .line-one {
    display: block; font-weight: 700; font-size: 54px; line-height: 1; letter-spacing: 0.5px;
  }
  .product-name .line-two {
    display: block; margin-top: 4px; font-weight: 700; font-size: 81px; line-height: 1;
    color: var(--accent);
  }
  .optin-form { position: absolute; left: 55px; top: 872px; width: 406px; }
  .field {
    height: 71px; padding: 0 0 16px 4px;
    border-bottom: 2px solid var(--paper);
    font-size: 22px; font-weight: 400; line-height: 1;
    display: flex; align-items: flex-end;
  }
  .field:first-child { height: 41px; }
  .submit-button {
    position: absolute; left: 59px; top: 1102px; width: 131px; height: 36px;
    border-radius: 18px; background: var(--accent); color: var(--paper);
    font-family: "Poppins", Arial, sans-serif; font-size: 24px; font-weight: 400;
    border: none; line-height: 36px; text-align: center;
  }
  .redeem-note {
    position: absolute; left: 667px; top: 1117px; width: 470px;
    font-size: 18px; font-weight: 300; line-height: 21px;
  }
</style>
</head>
<body>
  <main class="banner">
    <div class="workout-photo" role="img" aria-label="Group fitness class doing side plank exercises in a gym"></div>

    <svg class="header-shape" viewBox="0 0 1200 700" aria-hidden="true">
      <path fill="var(--accent)" d="M0 0 H958 L1050 200 Q1092 292 1000 336 L0 686 Z"/>
      <path fill="var(--ink)" d="M0 0 H934 L1024 205 Q1054 280 985 312 L0 659 Z"/>
    </svg>

    <h1 class="headline">WANT A GREAT OFFER?</h1>
    <p class="subhead">SUBSCRIBE TO OUR NEWSLETTER AND RECIEVE COMPLEMENTARY</p>

    <div class="product-photo" role="img" aria-label="Black smart fitness watch with step counter display"></div>

    <h2 class="product-name">
      <span class="line-one">SMART FITNESS</span>
      <span class="line-two">WATCH</span>
    </h2>

    <form class="optin-form">
      <label class="field">Name</label>
      <label class="field">Email</label>
      <label class="field">Phone</label>
    </form>

    <button class="submit-button" type="button">Submit</button>

    <p class="redeem-note">we will send an email and a text message with the offer and instructions on how to redeem</p>
  </main>
</body>
</html>
```